Need Help having my business card stand out

I am the owner of Birchway Canine Training and would like for my business cards to stand out. I have been trying to keep designing them myself but I can't get what I have in my head on the card. I will try my best to post templates that I like for inspirations. I want something unique but elegant. I don't want in to look cartoony or cheesy. It needs to pop in a pet shop but also in a coffee shop or gym.

Target Market(s)

Dog owners, Married ,No young kids Jr High school kids and up (maybe kids on the way) Executives, Stay at home moms/wives, Small business owners

Industry/Entity Type

Dog Training

Contact Information for Business Card

Lowell Spratt, 281-904-3376, info@birchwaycanine.example, www.birchwaycanine.example

Colors

Designer to choose colors to be used in the design.

Requirements
Must have
• my logo
Should not have
• Cursive lettering

```html
<!DOCTYPE html>
<html lang="en">
<head>
<meta charset="utf-8">
<title>Lowell Spratt · Birchway Canine Training</title>
<link rel="stylesheet" href="https://fonts.googleapis.com/css2?family=Roboto+Condensed:wght@400;700&display=swap">
<style>
  :root {
    --ink: #111111;
    --paper: #ffffff;
    --photo-light: #d9ddd2;
    --photo-mid: #8a8f6f;
    --photo-dark: #4a4a36;
    --shirt: #b23a3a;
  }
  * { margin: 0; padding: 0; box-sizing: border-box; }
  html, body {
    width: 1200px;
    height: 685px;
    overflow: hidden;
    background: var(--paper);
    font-family: "Roboto Condensed", "Arial Narrow", sans-serif;
  }
  .card {
    position: relative;
    width: 1200px;
    height: 685px;
    background: var(--paper);
    overflow: hidden;
  }
  .portrait {
    position: absolute;
    left: 8px;
    top: 0;
    width: 462px;
    height: 685px;
    border-radius: 20px 0 0 20px;
    background:
      radial-gradient(ellipse at 55% 55%, var(--shirt) 0%, rgba(178,58,58,0) 38%),
      linear-gradient(180deg, var(--photo-light) 0%, var(--photo-mid) 65%, var(--photo-dark) 100%);
  }
  .panel {
    position: absolute;
    left: 482px;
    top: 0;
    width: 718px;
    height: 685px;
    background: var(--ink);
    border-radius: 0 58px 58px 0;
  }
  .brand-flag {
    position: absolute;
    left: 736px;
    top: 0;
    width: 227px;
    height: 184px;
  }
  .brand-name {
    position: absolute;
    left: 736px;
    top: 58px;
    width: 227px;
    text-align: center;
    font-weight: 700;
    font-size: 34px;
    color: var(--ink);
    letter-spacing: 0.5px;
  }
  .identity {
    position: absolute;
    left: 539px;
    top: 326px;
    color: var(--paper);
    white-space: nowrap;
  }
  .identity .person {
    font-weight: 700;
    font-size: 41px;
    letter-spacing: 0.3px;
  }
  .identity .role {
    font-weight: 700;
    font-size: 25px;
    margin-left: 8px;
  }
  .rule {
    position: absolute;
    left: 530px;
    top: 396px;
    width: 670px;
    height: 3px;
    background: var(--paper);
  }
  .contacts {
    position: absolute;
    list-style: none;
    color: var(--paper);
    font-size: 20px;
  }
  .contacts li {
    display: flex;
    align-items: center;
    height: 40px;
    white-space: nowrap;
  }
  .contacts-left { left: 534px; top: 496px; }
  .contacts-right { left: 849px; top: 493px; }
  .contacts svg { width: 28px; height: 28px; margin-right: 22px; flex: none; }
</style>
</head>
<body>
  <div class="card">
    <div class="portrait" role="img" aria-label="Photo of the trainer kneeling on grass beside a shepherd dog"></div>

    <div class="panel"></div>

    <svg class="brand-flag" viewBox="0 0 227 184" aria-hidden="true">
      <polygon points="0,0 227,0 227,184 113.5,150 0,184" fill="#ffffff"/>
    </svg>
    <div class="brand-name">Birchway</div>

    <div class="identity">
      <span class="person">LOWELL SPRATT</span><span class="role">Head(Birchway)</span>
    </div>
    <div class="rule"></div>

    <ul class="contacts contacts-left">
      <li>
        <svg viewBox="0 0 28 28" aria-hidden="true">
          <circle cx="14" cy="14" r="13" fill="#ffffff"/>
          <path d="M10 8.5c.6-.6 1.4-.5 1.8.1l1.3 2c.3.5.2 1.1-.2 1.5l-.8.7c.7 1.5 1.8 2.6 3.3 3.3l.7-.8c.4-.4 1-.5 1.5-.2l2 1.3c.6.4.7 1.2.1 1.8l-1 1c-.8.8-2 .9-3 .4-2.9-1.4-5.2-3.7-6.6-6.6-.5-1-.4-2.2.4-3z" fill="#111111"/>
        </svg>
        281-904-3376
      </li>
      <li>
        <svg viewBox="0 0 28 28" aria-hidden="true">
          <circle cx="14" cy="14" r="13" fill="#ffffff"/>
          <circle cx="14" cy="14" r="2.6" fill="none" stroke="#111111" stroke-width="1.6"/>
          <path d="M16.6 11.5v3.6c0 1.4 2.6 1.6 2.6-1.1a5.2 5.2 0 1 0-2.2 4.3" fill="none" stroke="#111111" stroke-width="1.6" stroke-linecap="round"/>
        </svg>
        birchwaycanine
      </li>
      <li>
        <svg viewBox="0 0 28 28" aria-hidden="true">
          <circle cx="14" cy="14" r="13" fill="#ffffff"/>
          <rect x="8" y="10" width="12" height="8.5" rx="1" fill="#111111"/>
          <path d="M8.5 10.5l5.5 4.3 5.5-4.3" fill="none" stroke="#ffffff" stroke-width="1.2"/>
        </svg>
        info@birchwaycanine.example
      </li>
    </ul>

    <ul class="contacts contacts-right">
      <li>
        <svg viewBox="0 0 28 28" aria-hidden="true">
          <circle cx="14" cy="14" r="13" fill="#ffffff"/>
          <rect x="10.5" y="10.5" width="7" height="7" fill="#111111"/>
        </svg>
        Birchway Canine Training
      </li>
      <li>
        <svg viewBox="0 0 28 28" aria-hidden="true">
          <circle cx="14" cy="14" r="13" fill="#ffffff"/>
          <circle cx="14" cy="14" r="4" fill="#111111"/>
        </svg>
        www.birchwaycanine.example
      </li>
      <li>
        <svg viewBox="0 0 28 28" aria-hidden="true">
          <circle cx="14" cy="14" r="13" fill="#ffffff"/>
          <path d="M9 14h9M15 10.5l3.5 3.5-3.5 3.5" fill="none" stroke="#111111" stroke-width="2" stroke-linecap="round" stroke-linejoin="round"/>
        </svg>
        Birchway Canine Training
      </li>
    </ul>
  </div>
</body>
</html>
```